Fenwick Grading LTD - website for irrigation & Landscape Lighting & Buried service wire

Looking for a website to help promote my business with Irrigation (installation, service, etc) and buried service wire/drainage solutions.

Commercial/Residential

Landscape lighting.

I’ll get photos in the trucks and trailers to upload as well maybe the machine as well.

Target Market(s)

Homeowners who want green grass and beautiful gardens. Beautiful landscape lighting

Industry/Entity Type

Irrigation systems and landscape lighting and buried service wire to homes and offering Drainage soltions.

Coding

Coded - Design and coding required

Number of Pages Required

4 page

Colors
F0912C
F2A743
F7CA91
FBE8D2
FDF5EE

Requirements
Must have
• was hoping to link up my email on fenwickgrading@mailbox-example.net with the website if possible.
Nice to have
• Page for Irrigation, page for landscape lighting, page buried service wire & drainage soltions.

```html
<!DOCTYPE html>
<html lang="en">
<head>
<meta charset="utf-8">
<title>Fenwick Grading LTD</title>
<link href="https://fonts.googleapis.com/css2?family=Montserrat:wght@400;500;600;700&family=Oswald:wght@500&display=swap" rel="stylesheet">
<style>
:root{
  --orange:#f0912c;
  --orange-deep:#e8862a;
  --amber:#f2a743;
  --peach:#f7ca91;
  --cream:#fbe8d2;
  --ivory:#fdf5ee;
  --ink:#222222;
  --text:#555555;
  --black:#0b0b0b;
  --white:#ffffff;
}
*{margin:0;padding:0;box-sizing:border-box}
html,body{width:1200px;height:3971px;overflow:hidden;background:var(--white)}
body{font-family:"Montserrat",sans-serif;color:var(--ink)}
.page{position:relative;width:1200px;height:3971px;overflow:hidden}
.abs{position:absolute}
.btn{position:absolute;display:flex;align-items:center;justify-content:center;background:var(--orange);color:var(--white);font-size:12px;font-weight:600;text-decoration:none}

/* hero */
.hero{position:absolute;left:0;top:0;width:1200px;height:625px}
.hero svg{position:absolute;left:0;top:0}
.brand{position:absolute;left:142px;top:28px;display:flex;align-items:center;gap:10px;color:var(--white);font-size:20px;font-weight:700}
.brand .dot{width:18px;height:18px;border-radius:50%;background:var(--orange)}
.nav{position:absolute;top:36px;left:510px;display:flex;gap:28px;font-size:12px;font-weight:500;color:var(--white)}
.hero h1{position:absolute;left:142px;top:178px;width:470px;font-family:"Oswald",sans-serif;font-weight:500;font-size:36px;line-height:49px;color:var(--white)}
.hero p{position:absolute;left:142px;top:336px;width:455px;font-size:12px;line-height:22px;color:var(--white)}

/* services */
.svc-frame{position:absolute;background:var(--white);box-shadow:0 0 0 12px #f7f7f7,0 0 14px 12px rgba(0,0,0,.04)}
.svc-photo{position:absolute}
.svc-icon{position:absolute;width:64px;height:64px;border-radius:50%;background:var(--orange);display:flex;align-items:center;justify-content:center}
.svc-title{position:absolute;font-size:31px;font-weight:600;color:#333;white-space:nowrap}
.svc-text{position:absolute;width:380px;font-size:11.5px;line-height:22px;color:var(--text)}

/* about */
.about-card{position:absolute;left:609px;top:2278px;width:449px;height:454px;border-radius:9px;border:1px solid rgba(255,255,255,.35);background:linear-gradient(180deg,rgba(10,10,10,.92),rgba(20,20,20,.7));color:var(--white)}
.about-card .eyebrow{position:absolute;left:40px;top:50px;font-size:21px;font-weight:600}
.about-card h2{position:absolute;left:37px;top:92px;font-size:32px;font-weight:600;white-space:nowrap}
.about-card .rule{position:absolute;left:39px;top:146px;width:64px;height:3px;background:var(--orange)}
.about-card p{position:absolute;left:40px;width:380px;font-size:11.5px;line-height:20.5px}

/* reviews */
.section-title{position:absolute;left:0;width:1200px;text-align:center;font-size:33px;font-weight:600}
.rule-c{position:absolute;left:571px;width:58px;height:3px;background:var(--orange)}
.review{position:absolute;top:3023px;width:433px;height:255px;background:var(--white);box-shadow:0 2px 14px rgba(0,0,0,.1)}
.review .bar{position:absolute;left:20px;right:20px;bottom:-5px;height:5px;background:#666}
.review .avatar{position:absolute;left:178px;top:-31px;width:77px;height:77px;border-radius:50%;border:3px solid var(--orange);background:linear-gradient(180deg,var(--cream),var(--peach))}
.review h3{position:absolute;left:0;width:100%;top:64px;text-align:center;font-size:19px;font-weight:600}
.review p{position:absolute;left:30px;right:30px;top:100px;text-align:center;font-size:11.5px;line-height:20.5px;color:var(--text)}
.review .quote{position:absolute;right:14px;bottom:14px;font-family:"Oswald",sans-serif;font-size:70px;line-height:40px;color:var(--peach)}
.arrow{position:absolute;top:3128px;width:22px;height:26px}

/* cta + footer */
.footer{position:absolute;left:0;top:3561px;width:1200px;height:410px;background:var(--black)}
.cta{position:absolute;left:191px;top:3364px;width:818px;height:247px;background:var(--orange-deep)}
.cta .frame{position:absolute;left:53px;top:43px;width:712px;height:142px;border:1px solid rgba(255,255,255,.7)}
.cta h2{position:absolute;left:0;top:62px;width:818px;text-align:center;font-size:29px;line-height:42px;font-weight:600;color:#222}
.cta .btn{background:var(--white);color:#222}
.f-title{position:absolute;top:3674px;font-size:16px;font-weight:600;color:var(--white)}
.f-links{position:absolute;left:142px;top:3713px;list-style:none;font-size:11.5px;line-height:33px;color:var(--white)}
.f-links li::before{content:"›";margin-right:12px}
.contact{position:absolute;left:475px;display:flex;gap:14px;font-size:11.5px;line-height:19px;color:var(--white)}
.contact .ico{width:28px;height:28px;border-radius:50%;background:var(--orange);flex:none;display:flex;align-items:center;justify-content:center}
.contact b{font-weight:600;font-size:12.5px}
.f-brand{position:absolute;left:862px;top:3730px;display:flex;align-items:center;gap:10px;font-size:22px;font-weight:700;color:var(--orange)}
.f-brand .dot{width:20px;height:20px;border-radius:50%;background:var(--orange)}
.social{position:absolute;top:3822px;width:28px;height:28px;border-radius:50%;border:2px solid var(--orange)}
.f-rule{position:absolute;left:142px;top:3913px;width:916px;height:1px;background:#333}
.copy{position:absolute;left:0;top:3936px;width:1200px;text-align:center;font-size:11.5px;color:#ccc}
</style>
</head>
<body>
<div class="page">

  <!-- Hero -->
  <header class="hero">
    <svg width="1200" height="625" viewBox="0 0 1200 625" role="img" aria-label="Evening garden lawn with lit path lights and landscaped shrubs">
      <defs>
        <linearGradient id="heroFill" x1="0" y1="0" x2="1" y2="1">
          <stop offset="0" stop-color="#2c3a1c"/>
          <stop offset=".55" stop-color="#4b6a2a"/>
          <stop offset="1" stop-color="#2a3420"/>
        </linearGradient>
      </defs>
      <path d="M0 0H1200V543L600 617L0 543Z" fill="url(#heroFill)"/>
      <path d="M0 543L600 617L1200 543" fill="none" stroke="#f0912c" stroke-width="3"/>
    </svg>
    <div class="brand"><span class="dot"></span>Fenwick Grading LTD</div>
    <nav class="nav"><span>Home</span><span>Irrigation</span><span>Landscape Lighting</span><span>Wire &amp; Drainage</span></nav>
    <a class="btn" style="left:955px;top:26px;width:103px;height:37px">Contact Us</a>
    <h1>Transform Your Outdoor Space With Our Expert Irrigation And Lighting Solutions</h1>
    <p>Get the perfect blend of form and function with our state-of-the-art irrigation systems and landscape lighting.Trust our experienced team to deliver buried service wire and drainage solutions for your home</p>
    <a class="btn" style="left:142px;top:416px;width:103px;height:37px">Contact Us</a>
  </header>

  <!-- Irrigation -->
  <section>
    <div class="svc-frame" style="left:262px;top:705px;width:787px;height:405px"></div>
    <div class="svc-photo" role="img" aria-label="Sprinkler watering a lawn beside a gravel border" style="left:143px;top:742px;width:423px;height:331px;background:linear-gradient(160deg,#8a9a6a,#5f8a34 45%,#a39380)"></div>
    <div class="svc-icon" style="left:618px;top:760px"><svg width="30" height="30" viewBox="0 0 30 30"><path d="M5 24H25M9 24V14M21 24V14M9 14L5 7M9 14L13 7M21 14L17 7M21 14L25 7" stroke="#fff" stroke-width="2" fill="none" stroke-linecap="round"/></svg></div>
    <h2 class="svc-title" style="left:618px;top:838px">Irrigation Systems</h2>
    <p class="svc-text" style="left:618px;top:884px">Our irrigation systems are designed to provide your lawn and garden with the right amount of water, without wasting a single drop. With our expert installation and service, you can rest assured that your plants will receive the nourishment they need to thrive.</p>
    <a class="btn" style="left:618px;top:1007px;width:115px;height:37px">Learn More</a>
  </section>

  <!-- Landscape Lighting -->
  <section>
    <div class="svc-frame" style="left:149px;top:1196px;width:788px;height:404px"></div>
    <div class="svc-photo" role="img" aria-label="Lit garden pathway at night under trees" style="left:632px;top:1229px;width:425px;height:333px;background:radial-gradient(circle at 50% 45%,#c9b45a,#3c4a22 45%,#151a10)"></div>
    <div class="svc-icon" style="left:196px;top:1249px"><svg width="30" height="30" viewBox="0 0 30 30"><circle cx="15" cy="12" r="6" stroke="#fff" stroke-width="2" fill="none"/><path d="M12 20H18M13 24H17" stroke="#fff" stroke-width="2" stroke-linecap="round"/></svg></div>
    <h2 class="svc-title" style="left:196px;top:1326px">Landscape Lighting</h2>
    <p class="svc-text" style="left:196px;top:1372px">Our landscape lighting solutions are designed to enhance the beauty and functionality of your outdoor space. From subtle pathway lighting to dramatic spotlights, we'll work with you to create a lighting plan that meets your needs and complements your landscape</p>
    <a class="btn" style="left:196px;top:1501px;width:114px;height:37px">Learn More</a>
  </section>

  <!-- Service Wire & Drainage -->
  <section>
    <div class="svc-frame" style="left:259px;top:1684px;width:790px;height:404px"></div>
    <div class="svc-photo" role="img" aria-label="Crew laying buried service wire in a trench beside a home" style="left:140px;top:1718px;width:424px;height:333px;background:linear-gradient(120deg,#3a3128,#6b5a44 50%,#9aa07a)"></div>
    <div class="svc-icon" style="left:617px;top:1738px"><svg width="30" height="30" viewBox="0 0 30 30"><path d="M4 10H26M4 10V24H26V10" stroke="#fff" stroke-width="2" fill="none" stroke-linejoin="round"/><path d="M7 19C11 15 15 23 19 19S23 17 24 17" stroke="#fff" stroke-width="2" fill="none" stroke-linecap="round"/></svg></div>
    <h2 class="svc-title" style="left:617px;top:1815px">Service Wire &amp; Drainage</h2>
    <p class="svc-text" style="left:617px;top:1862px">Our team of experienced professionals will bury your service wire and install drainage with precision and care. We'll work with you to keep your yard dry and your home safely connected, with clean trenching and tidy restoration of your lawn</p>
    <a class="btn" style="left:617px;top:1985px;width:114px;height:37px">Learn More</a>
  </section>

  <!-- About -->
  <section>
    <div class="abs" role="img" aria-label="House with green lawn, trimmed hedges and red flower beds" style="left:0;top:2193px;width:1200px;height:626px;background:linear-gradient(180deg,#6f8a5a,#3f6a2c 55%,#2f5a22)"></div>
    <div class="about-card">
      <div class="eyebrow">About</div>
      <h2>Fenwick Grading Ltd</h2>
      <div class="rule"></div>
      <p style="top:164px">Lorem ipsum dolor sit amet, consectetur adipiscing elit sed do eiusmod tempor incididunt ut labore et dolore magna aliqua Ut enim ad minim veniam quis</p>
      <p style="top:232px">Lorem ipsum dolor sit amet, consectetur adipiscing elit sed do eiusmod tempor incididunt ut labore et dolore magna aliqua Ut enim ad minim veniam quis "Lorem ipsum dolor sit amet, consectetur adipiscing elit sed do eiusmod tempor incididunt ut labore et dolore magna aliqua</p>
      <a class="btn" style="left:39px;top:358px;width:103px;height:38px">Contact Us</a>
    </div>
  </section>

  <!-- Reviews -->
  <section>
    <h2 class="section-title" style="top:2902px">Customer Reviews</h2>
    <div class="rule-c" style="top:2964px"></div>
    <article class="review" style="left:143px">
      <div class="avatar" role="img" aria-label="Customer portrait"></div>
      <h3>Marcus Hale</h3>
      <p>Lorem Ipsum is simply dummy text of the printing and typesetting industry. Lorem Ipsum has been the industry's standard dummy text ever since the 1500s, when an unknown printer took a galley of type and scrambledstandard dummy text ever since standard dummy text ever since</p>
      <span class="quote">”</span>
      <div class="bar"></div>
    </article>
    <article class="review" style="left:625px">
      <div class="avatar" role="img" aria-label="Customer portrait"></div>
      <h3>Nora Pike</h3>
      <p>Lorem Ipsum is simply dummy text of the printing and typesetting industry. Lorem Ipsum has been the industry's standard dummy text ever since the 1500s, when an unknown printer took a galley of type and scrambled standard dummy text ever since standard dummy text ever since</p>
      <span class="quote">”</span>
      <div class="bar"></div>
    </article>
    <svg class="arrow" style="left:136px" viewBox="0 0 22 26"><path d="M14 8L9 13L14 18" stroke="#f0912c" stroke-width="2" fill="none"/></svg>
    <svg class="arrow" style="left:1046px" viewBox="0 0 22 26"><path d="M8 8L13 13L8 18" stroke="#f0912c" stroke-width="2" fill="none"/></svg>
  </section>

  <!-- Footer -->
  <footer>
    <div class="footer"></div>
    <div class="cta">
      <div class="frame"></div>
      <h2>Expertise In Irrigation Systems, Landscape<br>Lighting, And Service Wire &amp; Drainage</h2>
      <a class="btn" style="left:358px;top:168px;width:103px;height:36px">Contact Us</a>
    </div>

    <h3 class="f-title" style="left:142px">Quick Links</h3>
    <ul class="f-links">
      <li>Home</li><li>Irrigation</li><li>Landscape Lighting</li><li>Service Wire &amp; Drainage</li><li>Contact Us</li>
    </ul>

    <h3 class="f-title" style="left:473px">Contact Details</h3>
    <div class="contact" style="top:3716px">
      <span class="ico"><svg width="14" height="14" viewBox="0 0 14 14"><path d="M7 13C7 13 2 8 2 5A5 5 0 0 1 12 5C12 8 7 13 7 13Z" fill="#fff"/><circle cx="7" cy="5" r="1.8" fill="#f0912c"/></svg></span>
      <div>12 Lorem Imsum, Street Name,<br>City Name, Country - 12345</div>
    </div>
    <div class="contact" style="top:3772px">
      <span class="ico"><svg width="14" height="14" viewBox="0 0 14 14"><path d="M3 1L5.5 3.5L4 5.5C5 7.5 6.5 9 8.5 10L10.5 8.5L13 11L11 13C6 12.5 1.5 8 1 3Z" fill="#fff"/></svg></span>
      <div><b>Phone</b><br>123.456.7890</div>
    </div>
    <div class="contact" style="top:3827px">
      <span class="ico"><svg width="14" height="14" viewBox="0 0 14 14"><rect x="1.5" y="3" width="11" height="8" fill="#fff"/><path d="M1.5 3L7 7.5L12.5 3" stroke="#f0912c" stroke-width="1.2" fill="none"/></svg></span>
      <div><b>Email</b><br>fenwickgrading@mailbox-example.net</div>
    </div>

    <div class="f-brand"><span class="dot"></span>Fenwick Grading LTD</div>
    <span class="social" style="left:899px"></span>
    <span class="social" style="left:934px"></span>
    <span class="social" style="left:970px"></span>
    <span class="social" style="left:1005px"></span>

    <div class="f-rule"></div>
    <p class="copy">© 2024 Fenwick Grading Ltd . All Rights Reserved.</p>
  </footer>

</div>
</body>
</html>
```